Baby Adoption Announcement

I'm looking for a simple, understated and modern baby adoption announcement.

The baby is a boy, but I don't want anything that is blue or particularly boyish. No storks, baby baskets, rattles, or traditional baby announcement designs. No cutesy or busy designs.

Should measure 5.25 x 8.25 inches to fit in an A9 envelope.

Simple graphics MIGHT include birds, grasses, trees, rivers. I'm open to other ideas. Text can be a single color or multi colored. Graphics are not mandatory.

Since this is text heavy, I'd like the designer to be REALLY GOOD at choosing fonts and typesetting.

Text should read:

Memory answers us bright on your face—
Impossibly, we spoke and were silent
Together before all of this. (in italics)

Tobias Aldric Pelt Ostry
Born on March 16, 2012 in Boston, MA
and entrusted to us by his birthmother, Greta.

Named Tobias, which means God is with us, after Greta’s grandfather &
Aldric, after Al and St. Aldric of Myra

Requirements
Must have
• Should measure 5.25 x 8.25 inches to fit in A9 envelope.

Should not have
• The baby is a boy, but I don't want anything that is blue or particularly boyish. No storks, baby baskets, rattles, or traditional baby announcement designs. Nothing cutesy or busy.

```html
<!DOCTYPE html>
<html lang="en">
<head>
<meta charset="utf-8">
<title>Adoption Announcement – Tobias Aldric Pelt Ostry</title>
<link rel="stylesheet" href="https://fonts.googleapis.com/css2?family=Alex+Brush&family=Cinzel:wght@400;500&family=Marcellus&display=swap">
<style>
  :root {
    --paper: #f1e5d5;
    --card: #976616;
    --card-shadow: rgba(60, 40, 10, 0.45);
    --coral: #d86f60;
    --cream: #f2e6d6;
    --ink: #3f3a36;
    --wine: #8a2b45;
  }
  * { margin: 0; padding: 0; box-sizing: border-box; }
  html, body {
    width: 1200px;
    height: 897px;
    overflow: hidden;
    background: var(--paper);
  }
  .canvas {
    position: relative;
    width: 1200px;
    height: 897px;
  }
  .card {
    position: absolute;
    left: 25px;
    top: 80px;
    width: 1148px;
    height: 741px;
    background: var(--card);
    box-shadow: 4px 5px 6px var(--card-shadow);
  }
  .decor {
    position: absolute;
    left: 0;
    top: 0;
    width: 1200px;
    height: 897px;
  }
  .message {
    position: absolute;
    left: 308px;
    top: 182px;
    width: 588px;
    height: 538px;
    text-align: center;
    color: var(--ink);
  }
  .verse {
    font-family: "Alex Brush", cursive;
    font-size: 35px;
    line-height: 38px;
    margin-top: 66px;
  }
  .child-name {
    font-family: "Cinzel", serif;
    font-weight: 500;
    font-size: 24px;
    letter-spacing: 0.5px;
    color: var(--wine);
    margin-top: 40px;
    line-height: 34px;
  }
  .details {
    font-family: "Marcellus", serif;
    font-size: 21px;
    line-height: 36px;
  }
  .birth { margin-bottom: 27px; }
  .accent {
    font-family: "Cinzel", serif;
    font-weight: 500;
    font-size: 22px;
    color: var(--wine);
  }
  .birthmother {
    font-family: "Alex Brush", cursive;
    font-size: 28px;
    color: var(--wine);
  }
</style>
</head>
<body>
<main class="canvas">
  <div class="card"></div>

  <svg class="decor" viewBox="0 0 1200 897">
    <defs>
      <radialGradient id="ornament-glow" cx="50%" cy="50%" r="55%">
        <stop offset="0" stop-color="#e9cfae" stop-opacity="0.55"/>
        <stop offset="1" stop-color="#e9cfae" stop-opacity="0.12"/>
      </radialGradient>
    </defs>

    <rect class="frame" x="48" y="100" width="1104" height="700" fill="none" stroke="var(--coral)" stroke-width="8"/>

    <rect class="ornament-area" x="56" y="410" width="290" height="330" rx="40"
          fill="url(#ornament-glow)" role="img"
          aria-label="Dotted looping flight path with a small coral dragonfly"/>

    <rect class="ornament-area" x="860" y="176" width="284" height="616" rx="40"
          fill="url(#ornament-glow)" role="img"
          aria-label="Cream curling tree stems and swirls with a coral dragonfly on a dotted flight path"/>

    <rect class="panel" x="308" y="184" width="588" height="534" rx="62" ry="62"
          fill="var(--cream)" stroke="var(--coral)" stroke-width="8" stroke-dasharray="22 14"/>
  </svg>

  <section class="message">
    <p class="verse">Memory answers us bright on your face<br>Impossibly, we spoke and were silent<br>Together before all of this</p>
    <h1 class="child-name">Tobias Aldric Pelt Ostry</h1>
    <p class="details birth">Born on March 16, 2012 in Boston, MA<br>and entrusted to us by his birthmother, <span class="birthmother">Greta</span>.</p>
    <p class="details naming">Named Tobias, which means <span class="accent">God is with us</span><br>after Greta’s grandfather &amp;<br><span class="accent">aldric</span>, after Al and <span class="accent">St. Aldric of Myra</span></p>
  </section>
</main>
</body>
</html>
```